Hearthstead Insurance Provider Website

We are selling Hearthstead Insurance policy / tenants Policy/Flood Insurance in USA in few states and planning expand nationally.

Our target audience are two folds: Customers (Buy policies) and Insurance Agents who wants to work with us to sell our policies to customers. But website should focus 80% on customers and 20% on agents. So, more customer focused user experience. Please note that there is no direct buy option for customers. They always go through insurance agents.

Customer focused, educational that makes buyer journey easy. We don’t want to come off as trying sell something as there is no direct sales involved from website.

Target Market(s)

Homeowners in USA and Insurance agent who sells these insurance.

Industry/Entity Type

Insurance

Number of Pages Required

4 page

Font styles to use
Other font styles liked:
• Open to suggestions

Colors

Designer to choose colors to be used in the design.

Requirements
Must have
• Three most important things: Trustworthy, Authentic, Simple
• Please use colors form logo and grays
• We like: www.hollowmere.com
• https://www.quillfenbrook.com/
• We need Agent Look up tool on home page similar to what is shown on example sites.
• Design:
• Home Page - Open to Ideas
• Insurance (Products) Landing Page - Info similar to: https://www.quillfenbrook.com/insurance/
• Agents Page - https://www.quillfenbrook.com/agents/
• Claims Page - Information similar to: https://www.quillfenbrook.com/claims-center/
• Site Navigation:
• Home
• Insurance
• Claims
• Agents
• About Us
• Contact Us
Nice to have
• Elegant, minimal and clean design that reflects trust and authenticity.
Should not have
• Slider or rotating images - prefer flat design. Not over powering design.

```html
<!DOCTYPE html>
<html lang="en">
<head>
<meta charset="utf-8">
<title>Hearthstead Insurance Co.</title>
<link rel="stylesheet" href="https://fonts.googleapis.com/css2?family=Fira+Sans:wght@400;500;600&display=swap">
<style>
:root{
  --red:#d21f2e;
  --navy:#1d3a82;
  --ink:#2b2b2b;
  --text:#4a4a4a;
  --hero-bg:#e9ebec;
  --card-bg:#eef0f1;
  --foot-bg:#eef0f1;
  --line:#dcdfe1;
  --white:#ffffff;
}
*{box-sizing:border-box;margin:0;padding:0}
html,body{width:1108px;height:1200px;overflow:hidden}
body{font-family:"Fira Sans",sans-serif;color:var(--text);background:var(--foot-bg);position:relative}
a{color:inherit;text-decoration:none}
.hero{position:absolute;left:0;top:0;width:1108px;height:553px;background:radial-gradient(ellipse at 40% 40%,#f7f8f8 0%,var(--hero-bg) 70%);overflow:hidden}
.hero-red{position:absolute;left:790px;top:0;width:318px;height:553px;background:var(--red)}
.brand{position:absolute;left:160px;top:26px;display:flex;align-items:center;gap:8px}
.brand-mark{width:30px;height:30px;background:var(--navy)}
.brand-name{font-size:18px;font-weight:500;color:var(--navy);line-height:1;letter-spacing:.3px}
.brand-name small{display:block;font-size:11px;letter-spacing:2px;margin-top:2px}
.main-nav{position:absolute;top:33px;left:480px;display:flex;gap:21px;font-size:12.5px;color:#333}
.util-nav{position:absolute;top:28px;left:827px;display:flex;align-items:center;gap:14px;font-size:12.5px;color:var(--white)}
.login-btn{border:1px solid var(--white);padding:4px 10px}
.hero-photo{position:absolute;left:240px;top:86px;width:350px;height:467px;border-radius:170px 170px 0 0;background:linear-gradient(180deg,#c9885a 0%,#6f86c0 45%,#5f78b6 100%)}
.agent-card{position:absolute;left:634px;top:106px;width:314px;height:408px}
.agent-card svg{position:absolute;left:0;top:0}
.agent-inner{position:absolute;left:0;top:104px;width:314px;text-align:center}
.agent-inner h1{font-size:29px;font-weight:500;color:var(--ink)}
.agent-inner p{font-size:12px;line-height:18px;margin-top:12px;color:var(--text)}
.zip{display:block;margin:20px auto 0;width:182px;height:37px;border:1px solid #d8d8d8;border-radius:3px;background:#f1f1f1;font:12px "Fira Sans",sans-serif;padding-left:15px;color:#888;text-align:left;line-height:35px}
.btn{display:inline-block;background:var(--navy);color:var(--white);font-weight:500;font-size:13.5px;text-align:center;border-radius:3px;text-transform:uppercase}
.agent-inner .btn{width:182px;height:37px;line-height:37px;margin-top:7px}
.products{position:absolute;left:0;top:553px;width:1108px;height:375px;display:flex}
.product{position:relative;width:277px;height:375px;background:var(--card-bg);border-right:1px solid var(--line)}
.product:last-child{border-right:0}
.product-photo{position:absolute;left:0;top:0;width:100%;height:279px;clip-path:polygon(0 0,100% 0,100% 100%,50% 94%,0 100%)}
.p1{background:linear-gradient(160deg,#d9d6cf,#8a6a4c 60%,#6b6d72)}
.p2{background:linear-gradient(180deg,#6fa6d8,#4a4e55 55%,#8b9a7a)}
.p3{background:linear-gradient(160deg,#8d8f8e,#e0662a 55%,#6b3b2b)}
.p4{background:linear-gradient(160deg,#9c5a45,#c9b8a6 50%,#5a7f45)}
.product h2{position:absolute;top:293px;width:100%;text-align:center;font-size:19px;font-weight:500;color:var(--ink)}
.product p{position:absolute;top:322px;width:100%;text-align:center;font-size:12px;line-height:15.5px}
.footer-col{position:absolute;top:970px;font-size:12px;line-height:18px}
.footer-col h3{font-size:12px;font-weight:500;color:var(--ink);margin-bottom:13px}
.footer-col li{list-style:none}
.socials{display:flex;gap:6px;margin-top:10px}
.socials span{width:28px;height:28px;border:1.5px solid #555;border-radius:50%}
.footer-col .btn{width:130px;height:37px;line-height:37px;margin-top:18px}
.copyright{position:absolute;top:1126px;width:1108px;text-align:center;font-size:12px;line-height:18px}
</style>
</head>
<body>
<section class="hero">
  <div class="hero-red"></div>
  <div class="brand"><span class="brand-mark"></span><span class="brand-name">HEARTHSTEAD<small>INSURANCE CO.</small></span></div>
  <nav class="main-nav"><a href="#">Home</a><a href="#">Insurance</a><a href="#">About Us</a><a href="#">Claims</a><a href="#">Agents</a></nav>
  <nav class="util-nav"><a href="#">Career</a><a href="#" class="login-btn">Login</a></nav>
  <div class="hero-photo" role="img" aria-label="Smiling agent in a blue shirt holding a tablet"></div>
  <div class="agent-card">
    <svg width="314" height="408" viewBox="0 0 314 408">
      <polygon points="0,12 157,0 314,12 314,330 157,408 0,330" fill="#ffffff"/>
      <polygon points="10,22 157,10 304,22 304,323 157,396 10,323" fill="none" stroke="#dcdfe1" stroke-width="3"/>
    </svg>
    <div class="agent-inner">
      <h1>Find an Agent</h1>
      <p>Talk to one of our local independent<br>agencies to get a quote, ask questions<br>about coverage options &amp; more!</p>
      <div class="zip">ZIP Code</div>
      <a href="#" class="btn">Find an Agent</a>
    </div>
  </div>
</section>

<section class="products">
  <article class="product"><div class="product-photo p1" role="img" aria-label="Couple standing at the front door of their house"></div><h2>Homeowners</h2><p>Proin gravida nibh vel velit auctor<br>anean mauris accumsa velit.</p></article>
  <article class="product"><div class="product-photo p2" role="img" aria-label="Tall apartment buildings under a blue sky"></div><h2>Renters/Condo</h2><p>Proin gravida nibh vel velit auctor<br>anean mauris accumsa velit.</p></article>
  <article class="product"><div class="product-photo p3" role="img" aria-label="House roof burning with flames and smoke"></div><h2>Dwelling Fire</h2><p>Proin gravida nibh vel velit auctor<br>anean mauris accumsa velit.</p></article>
  <article class="product"><div class="product-photo p4" role="img" aria-label="Agent holding a folder outside a brick house"></div><h2>Agent Locator Tool</h2><p>Proin gravida nibh vel velit auctor<br>anean mauris accumsa velit.</p></article>
</section>

<footer>
  <div class="footer-col" style="left:158px"><h3>Contact Info</h3><p>1800 555 0142<br>info@hearthsteadinsurance.co</p><div class="socials"><span></span><span></span><span></span><span></span></div></div>
  <div class="footer-col" style="left:361px"><h3>Our Company</h3><ul><li>Home</li><li>Insurance</li><li>About Us</li><li>Claims</li><li>Agents</li></ul></div>
  <div class="footer-col" style="left:497px"><h3>Login to Your Account</h3><ul><li>Agents Login</li><li>Clients login</li></ul><a href="#" class="btn">Find an Agent</a></div>
  <div class="footer-col" style="left:678px"><h3>Customer Support</h3><ul><li>FAQs</li><li>Resources</li><li>Report a Claim</li><li>Find an Agent</li></ul></div>
  <div class="footer-col" style="left:834px"><h3>Connect With Us</h3><ul><li>Support</li><li>Careers</li></ul></div>
  <div class="copyright">Copyright ©2018 Hearthstead Insurance. All Rights Reserved<br>Terms of Use &nbsp;-&nbsp; Privacy Policy &nbsp;-&nbsp; Sitemap</div>
</footer>
</body>
</html>
```